DeskHarbor - Coworking website design

DeskHarbor is a new global coworking brand, growing fast and establishing stylish locations and communities that inspire innovation and collaboration all around the world.
The project includes a complete website design, focused on delivering the company’s values and messages, provide information to site visitors and to generate leads.

Please review the attached design brief, for more information.

Target Market(s)

Both men and women. Decision makers in:
Small & medium businesses in various fields, but mainly technology firms (Startups or established brands).
Global enterprises.
Dynamic “new generation” companies.
Press

Number of Pages Required

2 page

Requirements
Must have
• Project Scope & deliverables:
• Concept and design for :
• Home page
• Deliver the values mentioned above.
• Showcase the cities in which the company has locations in.
• Show customer testimonials.
• Provide an interface (form) for booking a tour and/or leaving contact details for more information (two alternatives)
• Coworking location page - Each location is in the coolest part of a different major city, and has its own address, set of amenities (kitchen, fast internet etc,), area information (public transportation accessibility, sites near by, bars and restaurants in walking distance) and pricing for private offices (based on number of people per office). Each location page must have an interface to book a location tour.
• Site Navigation (header & footer) - allow simple navigation between multiple city pages, location pages and homepage. Growth of up to 50 locations in 25 cities.
• The navigation should account for Navigation to additional pages (not commissioned in this project) such as:
• Locations
• Enterprise
• Special promotions
• Blog
• Contact us
• About us
• Note - the site should account for geolocation variable display, showing different content for different locations.
• Deliverables must include all editable graphic files (photoshop or similar), as follows:
• Home page - Desktop view (preferably both)
• Location page - Mobile web view (preferably both)
• Navigation - both options

```html
<!DOCTYPE html>
<html lang="en">
<head>
<meta charset="utf-8">
<title>DeskHarbor – Coworking</title>
<link rel="stylesheet" href="https://fonts.googleapis.com/css2?family=Roboto:wght@400;500;700&family=Roboto+Slab:wght@400;700&display=swap">
<style>
:root{
  --orange:#ef7838;
  --orange-dark:#e2692a;
  --black:#000;
  --ink:#333;
  --muted:#666;
  --light:#f3f3f5;
  --white:#fff;
  --line:#cfcfcf;
}
*{box-sizing:border-box;margin:0;padding:0}
html,body{width:1200px;height:3593px;overflow:hidden}
body{position:relative;background:var(--white);font-family:"Roboto",Arial,sans-serif;color:var(--ink)}
.abs{position:absolute}

/* header */
.site-header{position:absolute;left:0;top:0;width:1200px;height:96px;background:var(--black);border-bottom:2px solid #444}
.brand{position:absolute;left:86px;top:28px;font-family:"Roboto Slab",Georgia,serif;font-size:32px;color:var(--white)}
.main-nav{position:absolute;right:80px;top:40px;display:flex;gap:50px}
.main-nav a{font-family:"Roboto Slab",Georgia,serif;font-size:12px;color:var(--white);text-decoration:none;text-transform:uppercase;letter-spacing:.3px}

/* hero */
.hero{position:absolute;left:0;top:96px;width:1200px;height:555px}
.hero-photo{position:absolute;inset:0;background:linear-gradient(120deg,#4a3a30 0%,#7a6a5e 35%,#3d3632 60%,#5b4c42 100%)}
.hero-shade{position:absolute;inset:0;background:rgba(0,0,0,.35)}
.hero-title{position:absolute;left:0;width:1200px;top:180px;text-align:center;font-size:56px;font-weight:500;color:var(--white)}
.hero-sub{position:absolute;left:0;width:1200px;top:258px;text-align:center;font-size:12px;color:var(--white)}
.tour-form{position:absolute;left:151px;top:297px;width:898px;height:213px;background:rgba(90,90,90,.55)}
.field-label{position:absolute;font-size:12px;font-weight:700;color:var(--white);text-transform:uppercase}
.field{position:absolute;height:36px;background:var(--white);border-radius:2px}
.btn{display:block;background:var(--orange);color:var(--white);font-family:"Roboto Slab",Georgia,serif;font-size:13px;text-transform:uppercase;text-align:center;text-decoration:none}
.book-btn{position:absolute;left:747px;top:285px;width:132px;height:43px;line-height:43px;font-size:15px}

/* welcome */
.welcome{position:absolute;left:0;top:651px;width:1200px;height:463px;background:var(--light)}
.welcome-photo{position:absolute;left:135px;top:70px;width:330px;height:330px;border-radius:50%;border:4px solid var(--white);box-shadow:0 0 0 1px #ddd;background:radial-gradient(circle at 50% 60%,#b8917a 0%,#8d7c70 40%,#c9c3bd 75%)}
.welcome h2{position:absolute;left:522px;top:80px;font-family:"Roboto Slab",Georgia,serif;font-weight:400;font-size:29px;color:var(--ink)}
.rule{position:absolute;height:3px;width:102px;background:var(--orange)}
.welcome p{position:absolute;left:526px;width:514px;font-size:12px;line-height:24px;color:var(--muted)}

/* features timeline */
.timeline-line{position:absolute;left:598px;top:1185px;width:2px;height:1355px;background:var(--line)}
.timeline-cap{position:absolute;left:593px;width:12px;height:12px;border-radius:50%;background:var(--orange)}
.tick{position:absolute;left:588px;width:22px;height:22px}
.dot{position:absolute;left:596px;width:6px;height:6px;border-radius:50%;background:#aaa}
.feature-photo{position:absolute;width:450px;height:213px}
.feature h3{position:absolute;font-family:"Roboto Slab",Georgia,serif;font-weight:400;font-size:18px;color:var(--ink)}
.feature p{position:absolute;width:440px;font-size:11.5px;line-height:29px;color:var(--muted)}
.left h3,.left p{right:656px;text-align:right}
.right h3,.right p{left:640px;text-align:left}
.more{position:absolute;width:120px;height:43px;line-height:43px}
.left .more{left:424px}
.right .more{left:640px}

/* testimonials */
.testimonials{position:absolute;left:0;top:2599px;width:1200px;height:364px;background:linear-gradient(135deg,var(--orange) 0%,var(--orange-dark) 50%,var(--orange) 100%)}
.testimonials h2{position:absolute;left:0;width:1200px;top:36px;text-align:center;font-family:"Roboto Slab",Georgia,serif;font-weight:400;font-size:27px;color:var(--white)}
.quote-mark{position:absolute;font-family:"Roboto Slab",Georgia,serif;font-size:34px;color:var(--white)}
.quote{position:absolute;left:196px;top:130px;width:540px;font-size:12px;line-height:24px;color:var(--white)}
.author{position:absolute;left:196px;top:248px;font-size:14px;font-weight:700;color:var(--white);text-transform:uppercase}
.posted{position:absolute;left:200px;top:270px;font-size:11px;color:var(--white)}
.client-photo{position:absolute;left:808px;top:99px;width:194px;height:194px;border-radius:50%;border:4px solid var(--white);background:radial-gradient(circle at 50% 45%,#c89a7c 0%,#7a5744 60%,#dcdcd8 100%)}
.arrow{position:absolute;top:160px;width:24px;height:70px}

/* locations */
.locations{position:absolute;left:0;top:2963px;width:1200px;height:395px;background:#f5f5f6}
.world-map{position:absolute;left:50px;top:10px;width:1100px;height:375px;background:radial-gradient(ellipse at 50% 50%,#e6e6e8 0%,#ededee 60%,#f5f5f6 100%)}
.locations h2{position:absolute;left:0;width:1200px;top:58px;text-align:center;font-family:"Roboto Slab",Georgia,serif;font-weight:400;font-size:27px;color:var(--ink)}
.locations p{position:absolute;left:320px;width:560px;top:130px;text-align:center;font-size:12px;line-height:24px;color:var(--ink)}
.pin{position:absolute;width:24px;height:32px}

/* footer */
.site-footer{position:absolute;left:0;top:3358px;width:1200px;height:235px;background:var(--black)}
.social{position:absolute;left:390px;top:31px;display:flex;gap:14px}
.social span{width:58px;height:58px;border-radius:50%;border:1px solid #777;display:flex;align-items:center;justify-content:center}
.footer-rule{position:absolute;left:86px;top:113px;width:1028px;height:1px;background:#333}
.footer-nav{position:absolute;left:0;width:1200px;top:139px;text-align:center;font-family:"Roboto Slab",Georgia,serif;font-size:11px;color:var(--white);text-transform:uppercase}
.footer-nav a{color:var(--white);text-decoration:none;margin:0 22px}
.copyright{position:absolute;left:0;width:1200px;top:180px;text-align:center;font-family:"Roboto Slab",Georgia,serif;font-size:11px;color:#bbb}
</style>
</head>
<body>
<svg width="0" height="0" style="position:absolute">
  <defs>
    <symbol id="pin" viewBox="0 0 24 32"><path d="M12 1C6 1 1.5 5.5 1.5 11.5 1.5 19 12 31 12 31s10.5-12 10.5-19.5C22.5 5.5 18 1 12 1z" fill="currentColor"/><circle cx="12" cy="11.5" r="4.5" fill="#fff"/></symbol>
    <symbol id="tick" viewBox="0 0 22 22"><circle cx="11" cy="11" r="10" fill="#fff" stroke="#999" stroke-width="2"/><path d="M6.5 11.5l3 3 6-6.5" fill="none" stroke="#999" stroke-width="2.2"/></symbol>
  </defs>
</svg>

<header class="site-header">
  <div class="brand">DeskHarbor</div>
  <nav class="main-nav">
    <a href="#">Locations</a><a href="#">Enterprise</a><a href="#">Special Promotions</a><a href="#">Blog</a><a href="#">Contact Us</a><a href="#">About Us</a>
  </nav>
</header>

<section class="hero">
  <div class="hero-photo" role="img" aria-label="Team of coworkers talking around a shared table in a brick-walled office"></div>
  <div class="hero-shade"></div>
  <h1 class="hero-title">DeskHarbor</h1>
  <p class="hero-sub">Sed ut perspiciatis unde omnis iste natus error sit voluptatem accusantium doloremque laudantium, totam rem aperiam</p>
  <form class="tour-form">
    <span class="field-label" style="left:20px;top:30px">Name :</span>
    <span class="field-label" style="left:230px;top:30px">Email :</span>
    <span class="field-label" style="left:440px;top:30px">Phone :</span>
    <span class="field-label" style="left:666px;top:30px">Location :</span>
    <span class="field" style="left:18px;top:50px;width:202px"></span>
    <span class="field" style="left:228px;top:50px;width:202px"></span>
    <span class="field" style="left:438px;top:50px;width:216px"></span>
    <span class="field" style="left:662px;top:50px;width:218px">
      <svg style="position:absolute;right:10px;top:11px" width="10" height="14"><use href="#pin" color="#999"/></svg>
    </span>
    <span class="field-label" style="left:20px;top:98px">Message :</span>
    <span class="field" style="left:18px;top:118px;width:862px;height:56px"></span>
    <a class="btn book-btn" href="#">Book Now</a>
  </form>
</section>

<section class="welcome">
  <div class="welcome-photo" role="img" aria-label="Small team working together at a desk in a bright office"></div>
  <h2>Welcome to DeskHarbor</h2>
  <div class="rule" style="left:526px;top:130px"></div>
  <p style="top:160px">Coworking is a style of work that involves a shared working environment. Unlike in a typical officeenvironment, those coworking are usually employed by various organizations. Cowor king is a gathering of a group of people who are working independently, but who share values, and who are interested in the synergy that can happen from working with like-minded people, but about establishing and being part of a community.</p>
  <p style="top:308px">DeskHarbor is focused on a stylish work environment that includes private offices, with shared lounges,meeting rooms and kitchens (and NOT a shared open space for freelancers).</p>
</section>

<div class="timeline-line"></div>
<div class="timeline-cap" style="top:1177px"></div>
<div class="timeline-cap" style="top:2536px"></div>

<!-- row 1 -->
<div class="feature left">
  <h3 style="top:1212px">Inspire collaboration &amp; Innovation</h3>
  <div class="rule" style="left:478px;top:1247px;width:66px"></div>
  <p style="top:1266px">Sed ut perspiciatis unde omnis iste natus error sit voluptatem accusantium dol orem que laudantium, totam rem aperiam, eaque ipsa quae ab illo inventoreve ritatis et quasi architecto beatae vitae dicta sunt explicabo</p>
  <a class="btn more" style="top:1379px" href="#">Read More</a>
</div>
<div class="feature-photo" style="left:640px;top:1209px;background:linear-gradient(135deg,#2c2c2c,#4a4a40 50%,#2a2a2a)" role="img" aria-label="Glowing yellow light bulbs drawn on a chalkboard"></div>
<div class="dot" style="top:1292px"></div><svg class="tick" style="top:1301px"><use href="#tick"/></svg><div class="dot" style="top:1328px"></div>

<!-- row 2 -->
<div class="feature-photo" style="left:113px;top:1480px;background:linear-gradient(135deg,#c9c6c0,#8b7f74 50%,#b5aea6)" role="img" aria-label="Group gathered around a board labelled Ideas"></div>
<div class="feature right">
  <h3 style="top:1485px">Idea sharing</h3>
  <div class="rule" style="left:640px;top:1519px;width:66px"></div>
  <p style="top:1538px">Sed ut perspiciatis unde omnis iste natus error sit voluptatem accusantium dol orem que laudantium, totam rem aperiam, eaque ipsa quae ab illo inventoreve ritatis et quasi architecto beatae vitae dicta sunt explicabo</p>
  <a class="btn more" style="top:1651px" href="#">Read More</a>
</div>
<div class="dot" style="top:1561px"></div><svg class="tick" style="top:1570px"><use href="#tick"/></svg><div class="dot" style="top:1597px"></div>

<!-- row 3 -->
<div class="feature left">
  <h3 style="top:1758px">Be a part of an exclusive club</h3>
  <div class="rule" style="left:478px;top:1793px;width:66px"></div>
  <p style="top:1812px">Sed ut perspiciatis unde omnis iste natus error sit voluptatem accusantium dol orem que laudantium, totam rem aperiam, eaque ipsa quae ab illo inventoreve ritatis et quasi architecto beatae vitae dicta sunt explicabo</p>
  <a class="btn more" style="top:1925px" href="#">Read More</a>
</div>
<div class="feature-photo" style="left:640px;top:1755px;background:linear-gradient(135deg,#3e5660,#6c8a90 50%,#2f3c44)" role="img" aria-label="Busy open-plan coworking floor with people at desks"></div>
<div class="dot" style="top:1836px"></div><svg class="tick" style="top:1845px"><use href="#tick"/></svg><div class="dot" style="top:1872px"></div>

<!-- row 4 -->
<div class="feature-photo" style="left:113px;top:2028px;background:linear-gradient(135deg,#a9b4bc,#c9b79a 55%,#7d7366)" role="img" aria-label="Empty office with wooden desks and chairs by the windows"></div>
<div class="feature right">
  <h3 style="top:2033px">Realize your greatness</h3>
  <div class="rule" style="left:640px;top:2067px;width:66px"></div>
  <p style="top:2086px">Sed ut perspiciatis unde omnis iste natus error sit voluptatem accusantium dol orem que laudantium, totam rem aperiam, eaque ipsa quae ab illo inventoreve ritatis et quasi architecto beatae vitae dicta sunt explicabo</p>
  <a class="btn more" style="top:2197px" href="#">Read More</a>
</div>
<div class="dot" style="top:2107px"></div><svg class="tick" style="top:2116px"><use href="#tick"/></svg><div class="dot" style="top:2143px"></div>

<!-- row 5 -->
<div class="feature left">
  <h3 style="top:2290px">Style and design awareness</h3>
  <div class="rule" style="left:478px;top:2325px;width:66px"></div>
  <p style="top:2344px">Sed ut perspiciatis unde omnis iste natus error sit voluptatem accusantium dol orem que laudantium, totam rem aperiam, eaque ipsa quae ab illo inventoreve ritatis et quasi architecto beatae vitae dicta sunt explicabo</p>
  <a class="btn more" style="top:2457px" href="#">Read More</a>
</div>
<div class="feature-photo" style="left:640px;top:2287px;background:linear-gradient(135deg,#8a4a32,#b98a72 45%,#d8d4d0)" role="img" aria-label="Smiling coworkers with laptops in a brick-walled lounge"></div>
<div class="dot" style="top:2368px"></div><svg class="tick" style="top:2377px"><use href="#tick"/></svg><div class="dot" style="top:2404px"></div>

<section class="testimonials">
  <h2>Our Testimonials</h2>
  <div class="rule" style="left:558px;top:84px;width:84px;background:#fff"></div>
  <svg class="arrow" style="left:48px" viewBox="0 0 24 70"><path d="M20 2L4 35l16 33" fill="none" stroke="rgba(255,255,255,.5)" stroke-width="2"/></svg>
  <svg class="arrow" style="left:1128px" viewBox="0 0 24 70"><path d="M4 2l16 33L4 68" fill="none" stroke="rgba(255,255,255,.5)" stroke-width="2"/></svg>
  <span class="quote-mark" style="left:176px;top:100px">“</span>
  <p class="quote">Sed ut perspiciatis unde omnis iste natus error sit voluptatem accusantium doloremque laudantium, totam rem aperiam, eaque ipsa quae ab illo inventore veritatis et quasi architecto beatae vitae dicta sunt explicabo. Nemo enim ipsam voluptatem quia voluptas sit aspernatur aut odit aut fugit, sed quia consequuntur magni dolores eos qui ratione voluptatem sequi nesciunt.</p>
  <span class="quote-mark" style="left:582px;top:210px">”</span>
  <div class="author">Mara Lindqvist</div>
  <div class="posted">Posted On 07 Dec 2017</div>
  <div class="client-photo" role="img" aria-label="Portrait of a smiling client"></div>
</section>

<section class="locations">
  <div class="world-map" role="img" aria-label="Dotted world map showing DeskHarbor city locations"></div>
  <h2>DeskHarbor Locations</h2>
  <div class="rule" style="left:558px;top:104px;width:84px"></div>
  <p>Sed ut perspiciatis unde omnis iste natus error sit voluptatem accusantium doloremque laudantium, illo inventore veritatis et quasi architecto beatae vitae dicta sunt explicabo.</p>
  <svg class="pin" style="left:126px;top:32px;color:#e0b52c"><use href="#pin"/></svg>
  <svg class="pin" style="left:820px;top:32px;color:#e0b52c"><use href="#pin"/></svg>
  <svg class="pin" style="left:220px;top:46px;color:#6aa84f"><use href="#pin"/></svg>
  <svg class="pin" style="left:914px;top:46px;color:#6aa84f"><use href="#pin"/></svg>
  <svg class="pin" style="left:196px;top:144px;color:#2f6fb0"><use href="#pin"/></svg>
  <svg class="pin" style="left:890px;top:144px;color:#2f6fb0"><use href="#pin"/></svg>
  <svg class="pin" style="left:299px;top:118px;color:#a3286e"><use href="#pin"/></svg>
  <svg class="pin" style="left:994px;top:118px;color:#a3286e"><use href="#pin"/></svg>
  <svg class="pin" style="left:282px;top:240px;color:#b3233a"><use href="#pin"/></svg>
  <svg class="pin" style="left:977px;top:240px;color:#b3233a"><use href="#pin"/></svg>
  <svg class="pin" style="left:371px;top:256px;color:#2aa59a"><use href="#pin"/></svg>
  <svg class="pin" style="left:1066px;top:256px;color:#2aa59a"><use href="#pin"/></svg>
  <svg class="pin" style="left:622px;top:258px;color:#2aa59a"><use href="#pin"/></svg>
  <svg class="pin" style="left:287px;top:323px;color:#4fb08a"><use href="#pin"/></svg>
  <svg class="pin" style="left:982px;top:325px;color:#4fb08a"><use href="#pin"/></svg>
</section>

<footer class="site-footer">
  <div class="social">
    <span aria-label="Social link"></span>
    <span aria-label="Social link"></span>
    <span aria-label="Social link"></span>
    <span aria-label="Social link"></span>
    <span aria-label="Social link"></span>
    <span aria-label="Email"><svg width="20" height="14" viewBox="0 0 20 14"><rect x="1" y="1" width="18" height="12" fill="none" stroke="#fff" stroke-width="1.5"/><path d="M1 1l9 7 9-7" fill="none" stroke="#fff" stroke-width="1.5"/></svg></span>
  </div>
  <div class="footer-rule"></div>
  <nav class="footer-nav">
    <a href="#">Locations</a>|<a href="#">Enterprise</a>|<a href="#">Special Promotions</a>|<a href="#">Blog</a>|<a href="#">Contact Us</a>|<a href="#">About Us</a>
  </nav>
  <div class="copyright">© Copyrights 2017 DeskHarbor All Rights Reserved.</div>
</footer>
</body>
</html>
```